Lucky Harbour Fun Casino Entertainment

Looking to update my business card and make it look more modern, stand out and eye catching.
We are are fun casino business in Australia (primarily Sydney). Blackjack and Roulette are our most popular games although we have pretty much every game available for hire that you would find in a real casino. The final design would need to be sleek and appeal to the more upmarket corporate sector.
We mainly cater for Corporate Events, Private Parties, Fundraising Events, Team Building, Poker Tournaments
I think I'd prefer the colour Black.

Target Market(s)

High-end Corporate

Industry/Entity Type

Events

Contact Information for Business Card

Rob Kendall
Director
1300 482 617
0433 728 591
info@luckyharbour.com.au
www.luckyharbour.com.au
Facebook & Instagram @luckyharbourevents (proper social icons preferred)

Colors
000000
0255a3

Requirements
Must have
• Front side:
• Logo
• Contact details
• 'Australia's #1 Fun Casino Specialists'
• Back:
• Logo
Nice to have
• Back:
• Corporate Events
• Private Parties
• Poker Tournaments
• Fundraising
• Props & Theming
• Photo Booth
• Horse Racing Events
• The Vegas Sign attached, maybe on the back of the card in the background...?

```html
<!DOCTYPE html>
<html lang="en">
<head>
<meta charset="utf-8">
<title>Lucky Harbour Productions – Business Card</title>
<link rel="stylesheet" href="https://fonts.googleapis.com/css2?family=Libre+Baskerville:wght@700&family=Open+Sans:wght@400;600;700&display=swap">
<style>
  :root {
    --stage: #2b2d31;
    --card-black: #050505;
    --ink: #f4f4f4;
    --muted: #bdbdbd;
    --rule: #cfcfcf;
    --chip-gold: #f7a81b;
    --photo-dark: #0f0b09;
    --photo-warm: #4a3c31;
  }
  * { margin: 0; padding: 0; box-sizing: border-box; }
  html, body { width: 1200px; height: 900px; overflow: hidden; }
  body {
    background: var(--stage);
    font-family: "Open Sans", Arial, sans-serif;
    position: relative;
  }
  .card {
    position: absolute;
    top: 290px;
    width: 560px;
    height: 320px;
    border-radius: 4px;
    overflow: hidden;
    box-shadow: 0 12px 30px rgba(0,0,0,.45);
  }
  .card--front { left: 30px; background: var(--card-black); color: var(--ink); }
  .card--back { left: 610px; }

  .brand {
    position: absolute;
    display: flex;
    align-items: center;
    gap: 10px;
  }
  .brand__mark {
    flex: none;
    border-radius: 50%;
    border: 5px solid var(--chip-gold);
  }
  .brand__name {
    font-weight: 700;
    color: var(--chip-gold);
    text-transform: uppercase;
    line-height: 1.1;
    letter-spacing: .4px;
  }
  .card--front .brand { left: 38px; top: 112px; }
  .card--front .brand__mark { width: 40px; height: 40px; }
  .card--front .brand__name { font-size: 15px; }

  .tagline {
    position: absolute;
    left: 38px;
    top: 166px;
    width: 210px;
    font-size: 10px;
    letter-spacing: .3px;
    color: var(--muted);
  }

  .divider {
    position: absolute;
    left: 262px;
    top: 48px;
    width: 1.5px;
    height: 190px;
    background: var(--rule);
  }

  .contact { position: absolute; left: 284px; top: 62px; }
  .contact__name {
    font-family: "Libre Baskerville", "Times New Roman", serif;
    font-weight: 700;
    font-size: 24px;
    letter-spacing: .3px;
  }
  .contact__role {
    font-size: 15px;
    letter-spacing: .5px;
    margin-top: 2px;
    padding-bottom: 6px;
    border-bottom: 1.5px solid var(--rule);
    display: inline-block;
  }
  .contact__list { list-style: none; margin-top: 10px; }
  .contact__item {
    display: flex;
    align-items: center;
    gap: 8px;
    font-size: 15px;
    line-height: 24px;
  }
  .contact__icon { width: 14px; height: 14px; flex: none; }
  .social-dot {
    width: 12px; height: 12px; border-radius: 50%;
    background: var(--ink); flex: none; margin: 0 1px;
  }

  .website {
    position: absolute;
    left: 38px;
    bottom: 34px;
    font-size: 15px;
    letter-spacing: .3px;
  }

  .backdrop {
    position: absolute; inset: 0;
    background: linear-gradient(165deg, var(--photo-dark) 0%, var(--photo-warm) 55%, var(--photo-dark) 100%);
  }
  .card--back .brand {
    left: 50%; top: 50%;
    transform: translate(-50%, -50%);
  }
  .card--back .brand__mark { width: 70px; height: 70px; border-width: 7px; }
  .card--back .brand__name { font-size: 30px; }
</style>
</head>
<body>

  <section class="card card--front" aria-label="Business card front">
    <div class="brand">
      <span class="brand__mark"></span>
      <span class="brand__name">Lucky Harbour<br>Productions</span>
    </div>
    <p class="tagline">Australia's #1 Fun Casino Specialists</p>

    <span class="divider"></span>

    <div class="contact">
      <p class="contact__name">Rob Kendall</p>
      <p class="contact__role">DIRECTOR</p>
      <ul class="contact__list">
        <li class="contact__item">
          <svg class="contact__icon" viewBox="0 0 14 14"><circle cx="7" cy="7" r="7" fill="#f4f4f4"/><path d="M4.6 3.6l1.4 1.6-.7 1c.5 1 1.3 1.8 2.3 2.3l1-.7 1.6 1.4-.9 1.2C6.6 10.2 3.8 7.4 3.6 4.5z" fill="#050505"/></svg>
          1300 482 617
        </li>
        <li class="contact__item">
          <span class="contact__icon"></span>
          0433 728 591
        </li>
        <li class="contact__item">
          <svg class="contact__icon" viewBox="0 0 14 14"><circle cx="7" cy="7" r="7" fill="#f4f4f4"/><rect x="3.5" y="4.5" width="7" height="5" fill="none" stroke="#050505" stroke-width="1"/><path d="M3.5 4.5L7 7.3l3.5-2.8" fill="none" stroke="#050505" stroke-width="1"/></svg>
          info@luckyharbour.com.au
        </li>
        <li class="contact__item">
          <span class="social-dot"></span>
          @luckyharbourevents
        </li>
      </ul>
    </div>

    <p class="website">www.luckyharbour.com.au</p>
  </section>

  <section class="card card--back" aria-label="Business card back">
    <div class="backdrop" role="img" aria-label="Dark blurred photo of warm out-of-focus casino lights"></div>
    <div class="brand">
      <span class="brand__mark"></span>
      <span class="brand__name">Lucky Harbour<br>Productions</span>
    </div>
  </section>

</body>
</html>
```